Human Resource Consulting practice needs a business card design

We need a business card design (double sided colour) for our Human Resource (HR) consulting practice in regional New South Wales, australia. Our business name is Staff Compass. We support small and medium business across the Mid North Coast of New South Wales by providing them with outsourced HR support, services and products to help them achieve compliance with workplace legislation and across all areas of the employment lifecycle from recruitment to termination and everything in between. Our corporate colours are hot pink and black. The final design should communicate professionalism, trust, people focus.
I have attached the current (old) business card for your reference.

Target Market(s)

Business owners and high level managers

Industry/Entity Type

Business

Contact Information for Business Card

Name
Title
Phone no
Mobile no
Address
PO Box
email address
website

Colors
e34197

Requirements
Must have
• Tempate for changing business card personal details including Name, position title, mobile number, email address.
• Keep current logo and colours as per attached
• Logo must be presented in 2 colours or black only not white
Nice to have
• One side logo and graphic only other side logo and personal details
Should not have
• Should not be the same as the current version (attached) but a modern interpretation.
• Does not need a busy reverse side with our list of services as per current version. I feel this is too busy.
• No photos

```html
<!DOCTYPE html>
<html lang="en">
<head>
<meta charset="utf-8">
<title>Staff Compass – Business Card</title>
<link href="https://fonts.googleapis.com/css2?family=Michroma&display=swap" rel="stylesheet">
<style>
  :root {
    --hot-pink: #e314b4;
    --pink-soft: #e34197;
    --card-black: #0c0c0c;
    --ink-white: #f4f4f4;
    --ink-grey: #b9b9b9;
    --stage: #e8e5e1;
  }
  * { margin: 0; padding: 0; box-sizing: border-box; }
  html, body {
    width: 1200px; height: 892px; overflow: hidden;
    background: var(--stage);
    font-family: "Michroma", "Arial", sans-serif;
  }
  .sheet {
    position: relative; width: 1200px; height: 892px;
    display: flex; justify-content: center; align-items: center; gap: 100px;
  }
  .card {
    position: relative; width: 340px; height: 570px;
    border-radius: 18px; overflow: hidden;
    background: var(--card-black);
    box-shadow: 0 10px 30px rgba(0,0,0,.18);
  }
  .band {
    position: absolute; left: 0; right: 0; height: 62px;
    background: var(--hot-pink);
  }
  .band--top { top: 0; }
  .band--bottom { bottom: 0; }

  /* front */
  .brand {
    position: absolute; left: 34px; top: 112px;
    display: flex; align-items: center; gap: 10px;
    font-size: 26px; color: var(--hot-pink); letter-spacing: .5px;
  }
  .brand__dot { width: 12px; height: 12px; background: var(--ink-white); }
  .person { position: absolute; left: 34px; top: 236px; }
  .person__name { font-size: 25px; color: var(--hot-pink); letter-spacing: 1px; }
  .person__title { margin-top: 6px; font-size: 9px; color: var(--ink-grey); letter-spacing: 1.5px; text-transform: uppercase; }
  .contact { position: absolute; left: 34px; top: 330px; list-style: none; }
  .contact__item {
    display: flex; align-items: center; gap: 10px;
    font-size: 11.5px; color: var(--ink-white); line-height: 22px;
  }
  .contact__icon { width: 15px; height: 15px; flex: none; }
  .contact__address { margin-top: 4px; font-size: 11.5px; color: var(--ink-white); line-height: 19px; }

  /* back */
  .brand--back {
    position: absolute; left: 50%; top: 50%;
    transform: translate(-50%, -50%) rotate(90deg);
    white-space: nowrap; font-size: 40px; color: var(--ink-white);
    display: flex; align-items: center; gap: 14px;
  }
  .brand--back .brand__dot { width: 16px; height: 16px; background: var(--hot-pink); }
</style>
</head>
<body>
<main class="sheet">

  <section class="card card--front" aria-label="Card front">
    <div class="band band--top"></div>

    <div class="brand">
      <span class="brand__dot"></span>
      <span class="brand__name">Staff Compass</span>
    </div>

    <div class="person">
      <p class="person__name">Maren Holt</p>
      <p class="person__title">Principal Consultant</p>
    </div>

    <ul class="contact">
      <li class="contact__item">
        <svg class="contact__icon" viewBox="0 0 16 16"><rect width="16" height="16" rx="2" fill="#e314b4"/><path d="M5 4h2l1 2-1 1a6 6 0 0 0 2 2l1-1 2 1v2c-4 0-7-3-7-7z" fill="#fff"/></svg>
        <span>02 5550 1427</span>
      </li>
      <li class="contact__item">
        <svg class="contact__icon" viewBox="0 0 16 16"><rect width="16" height="16" rx="2" fill="#e314b4"/><rect x="5" y="3" width="6" height="10" rx="1" fill="#fff"/><rect x="6" y="4.5" width="4" height="6" fill="#e314b4"/></svg>
        <span>0400 555 318</span>
      </li>
      <li class="contact__item">
        <svg class="contact__icon" viewBox="0 0 16 16"><rect width="16" height="16" rx="2" fill="#e314b4"/><rect x="4" y="7" width="8" height="5" fill="#fff"/><rect x="5.5" y="3.5" width="5" height="3.5" fill="#fff"/></svg>
        <span>02 5550 1428</span>
      </li>
      <li class="contact__item">
        <svg class="contact__icon" viewBox="0 0 16 16"><rect width="16" height="16" rx="2" fill="#e314b4"/><circle cx="8" cy="8" r="4.5" fill="none" stroke="#fff" stroke-width="1.3"/><path d="M3.5 8h9M8 3.5v9" stroke="#fff" stroke-width="1"/></svg>
        <span>www.staffcompass.com.au</span>
      </li>
      <li class="contact__item">
        <svg class="contact__icon" viewBox="0 0 16 16"><rect width="16" height="16" rx="2" fill="#e314b4"/><rect x="3.5" y="5" width="9" height="6" fill="#fff"/><path d="M3.5 5l4.5 3.5L12.5 5" fill="none" stroke="#e314b4" stroke-width="1"/></svg>
        <span>maren@staffcompass.com.au</span>
      </li>
      <li class="contact__address">PO Box 218, Lakeview,<br>NSW 2480</li>
    </ul>

    <div class="band band--bottom"></div>
  </section>

  <section class="card card--back" aria-label="Card back">
    <div class="band band--top"></div>
    <div class="brand brand--back">
      <span class="brand__dot"></span>
      <span class="brand__name">Staff Compass</span>
    </div>
    <div class="band band--bottom"></div>
  </section>

</main>
</body>
</html>
```